Accountability Project Graphics

I want to create 10 social media graphics (new Instagram size 4:5 (1080 x 1350 pixels) focusing on our Quilvo Accountability App, using any of the 3 pictures attached. Use the attached pics only, NO RANDOM STOCK PHOTOGRAPHY. For the color scheme, use the landing page colors/fonts (attached).
You can add any of the 3 photos attached but I mainly need BOLD text that includes these headlines and sub-headlines on them.
Please NOTE for all the headlines below, also add this sub-headline on each graphic:
Stay Consistent with RT in Your Pocket!
Here are the headlines:
• Stop Starting Over Every Monday
• You don't need more willpower. You need more support
• Built for women who are tired of doing this alone
• When Motivation Fades, RT Checks In
• The Support System You've Been Missing
• Support When Motivation Disappears
• What if RT Checked in Every Day?
• The Missing Piece Isn't Another Diet
• Eat the food you love. Stay accountable every day.
• One Bad Meal Doesn't Mean You Failed
women over 40 trying to lose weight

```html
<!DOCTYPE html>
<html lang="en">
<head>
<meta charset="utf-8">
<title>Quilvo · Stop Starting Over Every Monday</title>
<link rel="stylesheet" href="https://fonts.googleapis.com/css2?family=Source+Serif+4:opsz,wght@8..60,700;8..60,800;8..60,900&family=Montserrat:wght@400;500;700;800&display=swap">
<style>
  :root {
    --ink: #22102e;
    --rose: #d9437a;
    --rose-soft: #ea7fa3;
    --blush-top: #fbe9ee;
    --blush-bottom: #f8d3de;
    --white: #ffffff;
    --glow: rgba(255, 240, 244, 0.7);
  }
  * { margin: 0; padding: 0; box-sizing: border-box; }
  html, body { width: 900px; height: 1200px; overflow: hidden; }
  body {
    position: relative;
    background: linear-gradient(160deg, var(--blush-top) 0%, #fbe2e9 45%, var(--blush-bottom) 100%);
    font-family: "Montserrat", sans-serif;
    color: var(--ink);
  }
  .halo {
    position: absolute; left: 428px; top: 165px;
    width: 450px; height: 450px; border-radius: 50%;
    background: var(--glow);
  }
  .portrait {
    position: absolute; left: 480px; top: 262px;
    width: 420px; height: 938px;
    border-radius: 200px 0 0 0;
    background: linear-gradient(180deg, rgba(40,22,34,0.0) 0%, rgba(60,28,44,0.35) 18%, rgba(34,20,30,0.75) 45%, rgba(120,20,40,0.7) 62%, rgba(30,18,26,0.85) 100%);
  }
  .tag {
    position: absolute; left: 52px; top: 62px;
    height: 41px; padding: 0 20px;
    display: flex; align-items: center;
    background: var(--white);
    border: 2px solid #f3b6c9;
    border-radius: 21px;
    color: var(--rose);
    font-weight: 700; font-size: 15px; letter-spacing: 0.5px;
    white-space: nowrap;
  }
  .headline {
    position: absolute; left: 54px; top: 126px;
    font-family: "Source Serif 4", serif;
    font-weight: 900; font-size: 108px; line-height: 90px;
    letter-spacing: -3.5px;
    color: var(--ink);
  }
  .headline .accent { color: var(--rose); font-weight: 800; }
  .rule { position: absolute; }
  .subline {
    position: absolute; left: 58px; top: 662px;
    font-family: "Source Serif 4", serif;
    font-weight: 700; font-size: 28px; line-height: 38px;
    color: var(--ink);
  }
  .subline .accent { color: var(--rose); }
  .subline-heart { position: absolute; left: 310px; top: 728px; }
  .calls {
    position: absolute; left: 58px; top: 846px;
    display: flex; align-items: center;
  }
  .calls-icon {
    width: 79px; height: 70px; border-radius: 12px;
    background: var(--rose-soft);
    display: flex; align-items: center; justify-content: center;
  }
  .calls-divider { width: 2px; height: 66px; background: var(--rose-soft); margin: 0 16px 0 19px; }
  .calls-text { font-size: 18px; line-height: 25px; font-weight: 500; color: var(--ink); }
  .bubble-small {
    position: absolute; left: 77px; top: 978px;
    height: 42px; padding: 0 19px;
    display: flex; align-items: center;
    background: var(--white);
    border-radius: 20px;
    box-shadow: 0 3px 10px rgba(150, 60, 90, 0.12);
    font-weight: 700; font-size: 18px; color: var(--ink);
  }
  .bubble-small .speaker { color: var(--rose); margin-right: 6px; }
  .bubble-large { position: absolute; left: 62px; top: 1019px; }
  .bubble-text {
    position: absolute; left: 92px; top: 1054px;
    font-family: "Source Serif 4", serif;
    font-weight: 700; font-size: 37px; color: var(--ink);
  }
</style>
</head>
<body>
  <div class="halo"></div>
  <div class="portrait" role="img" aria-label="Photo of RT smiling with hand on hip, dressed in black lace top and black jeans, leaning on a red pool table"></div>

  <div class="tag">QUILVO · STAY CONSISTENT WITH RT IN YOUR POCKET!</div>

  <h1 class="headline">Stop<br>Starting<br>Over<br><span class="accent">Every<br>Monday.</span></h1>

  <svg class="rule" style="left:56px;top:614px" width="260" height="14" viewBox="0 0 260 14">
    <path d="M2 10 Q130 2 258 5" stroke="var(--rose)" stroke-width="3" fill="none" stroke-linecap="round"/>
  </svg>

  <p class="subline">Built for women<br>who are tired of<br><span class="accent">doing this alone.</span></p>
  <svg class="subline-heart" width="44" height="54" viewBox="0 0 44 54">
    <path d="M20 50 C8 34 2 24 4 14 C6 4 17 3 20 14 C24 2 40 4 40 16 C40 28 28 40 20 50" stroke="var(--rose)" stroke-width="2.5" fill="none" stroke-linecap="round"/>
  </svg>

  <svg class="rule" style="left:56px;top:789px" width="250" height="12" viewBox="0 0 250 12">
    <path d="M2 8 Q125 3 248 5" stroke="var(--rose)" stroke-width="2.5" fill="none" stroke-linecap="round"/>
  </svg>

  <div class="calls">
    <div class="calls-icon">
      <svg width="44" height="44" viewBox="0 0 24 24" fill="none">
        <path d="M6.6 3.5 8.9 3c.5-.1 1 .2 1.2.7l1 2.7c.2.5 0 1-.4 1.3L9.3 8.8a11 11 0 0 0 5.9 5.9l1.1-1.4c.3-.4.8-.6 1.3-.4l2.7 1c.5.2.8.7.7 1.2l-.5 2.3c-.1.5-.6.9-1.100.9C11 18.3 5.7 13 5.7 4.6c0-.5.4-1 .9-1.1Z" fill="#fff"/>
        <path d="M14 4.5a5.5 5.5 0 0 1 5.5 5.5M14 7.5a2.5 2.5 0 0 1 2.5 2.5M14 1.5a8.5 8.5 0 0 1 8.5 8.5" stroke="#fff" stroke-width="1.5" stroke-linecap="round"/>
      </svg>
    </div>
    <div class="calls-divider"></div>
    <p class="calls-text">Weekly<br>calls from RT</p>
  </div>

  <div class="bubble-small"><span class="speaker">RT:</span>You good, sis?</div>

  <svg class="bubble-large" width="398" height="140" viewBox="0 0 398 140">
    <path d="M22 2 H376 Q396 2 396 22 V112 Q396 132 376 132 H34 L3 138 L3 22 Q3 2 22 2 Z" fill="#fde9ef" stroke="#ffffff" stroke-width="2"/>
    <path d="M52 115 Q180 104 300 108 M60 112 Q190 100 312 104" stroke="var(--rose)" stroke-width="3" fill="none" stroke-linecap="round"/>
    <path d="M333 97 C322 82 316 72 318 62 C320 52 330 52 333 62 C336 50 350 52 350 64 C350 76 340 86 333 97" stroke="var(--rose)" stroke-width="2.5" fill="none" stroke-linecap="round"/>
  </svg>
  <p class="bubble-text">You’ve got this!</p>
</body>
</html>
```